Carpet cleaning company focused on high quality needs business cards

We are a growing company that just merged with another company and need to design a new business card. We do both residential as well as commercial cleaning. We do carpet, tile & grout, upholstery, hard floors, and stain & pet odor removal. We treat our customers like family and strive to achieve outstanding results with every job.

```html
<!DOCTYPE html>
<html lang="en">
<head>
<meta charset="utf-8">
<title>Kindred Steam Care – Business Card</title>
<link href="https://fonts.googleapis.com/css2?family=Montserrat:wght@500;600;800&display=swap" rel="stylesheet">
<style>
  :root {
    --brand-red: #ec4a44;
    --ink: #1f1f22;
    --paper: #ffffff;
    --backdrop: #2a2b2f;
    --mascot-blue: #2f7fc0;
    --mascot-tan: #c39a5c;
  }
  * { box-sizing: border-box; margin: 0; padding: 0; }
  html, body {
    width: 1200px; height: 900px; overflow: hidden;
    background: var(--backdrop);
    font-family: "Montserrat", sans-serif;
  }
  .card {
    position: absolute;
    left: 240px;
    width: 720px; height: 412px;
    border-radius: 26px;
    overflow: hidden;
  }
  .card--front { top: 30px; background: var(--brand-red); }
  .card--back { top: 458px; background: var(--paper); }

  /* Front */
  .front-mascot {
    position: absolute; left: 170px; top: 110px;
    width: 190px; height: 190px; border-radius: 14px;
    background: linear-gradient(150deg, var(--mascot-blue), #c9705a 60%, var(--mascot-tan));
    opacity: .85;
  }
  .front-wordmark {
    position: absolute; left: 390px; top: 150px;
    display: flex; align-items: center; gap: 14px;
  }
  .wordmark-dot {
    width: 22px; height: 22px; border-radius: 50%;
    background: var(--ink); flex: none;
  }
  .wordmark-name {
    font-weight: 800; color: var(--ink);
    font-size: 34px; line-height: 1.05; text-transform: uppercase;
  }

  /* Back */
  .back-burst {
    position: absolute; left: 120px; bottom: 0;
    width: 0; height: 0;
    border-left: 220px solid transparent;
    border-bottom: 260px solid var(--brand-red);
  }
  .back-mascot {
    position: absolute; left: -20px; top: 120px;
    width: 360px; height: 310px;
    border-radius: 0 40px 0 0;
    background: linear-gradient(160deg, #e8e8e8 0%, var(--mascot-blue) 40%, var(--mascot-tan) 80%);
    opacity: .9;
  }
  .back-info {
    position: absolute; left: 400px; top: 40px; width: 300px;
  }
  .back-info .wordmark-name { font-size: 26px; }
  .person-name {
    margin-top: 26px;
    color: var(--brand-red); font-weight: 800; font-size: 28px;
  }
  .person-title { font-size: 15px; font-weight: 500; color: var(--ink); margin-top: 4px; }
  .address { margin-top: 16px; font-size: 15px; line-height: 1.35; color: var(--ink); font-weight: 500; }
  .contact-list { list-style: none; margin-top: 16px; }
  .contact-list li {
    display: flex; align-items: center; gap: 10px;
    font-size: 15px; line-height: 1.6; color: var(--ink); font-weight: 500;
  }
  .contact-list svg { width: 14px; height: 14px; fill: var(--brand-red); flex: none; }
</style>
</head>
<body>

<section class="card card--front" aria-label="Card front">
  <div class="front-mascot" role="img" aria-label="Illustrated cleaning technician holding a steam wand"></div>
  <div class="front-wordmark">
    <span class="wordmark-dot"></span>
    <span class="wordmark-name">Kindred<br>Steam Care</span>
  </div>
</section>

<section class="card card--back" aria-label="Card back">
  <div class="back-burst"></div>
  <div class="back-mascot" role="img" aria-label="Illustrated cleaning technician with a steam wand and hose"></div>

  <div class="back-info">
    <div class="front-wordmark" style="position:static">
      <span class="wordmark-dot"></span>
      <span class="wordmark-name">Kindred<br>Steam Care</span>
    </div>
    <p class="person-name">Daniel Mercer</p>
    <p class="person-title">CEO</p>
    <p class="address">418 Elm Park Ave, #112<br>Fairview, OH 43990</p>
    <ul class="contact-list">
      <li>
        <svg viewBox="0 0 16 16" aria-hidden="true"><path d="M3 1h3l1 4-2 1a9 9 0 0 0 5 5l1-2 4 1v3a2 2 0 0 1-2 2A13 13 0 0 1 1 3a2 2 0 0 1 2-2z"/></svg>
        555 310-4476
      </li>
      <li>
        <svg viewBox="0 0 16 16" aria-hidden="true"><path d="M4 0h8a1 1 0 0 1 1 1v14a1 1 0 0 1-1 1H4a1 1 0 0 1-1-1V1a1 1 0 0 1 1-1zm1 2v10h6V2zm3 11a1 1 0 1 0 0 2 1 1 0 0 0 0-2z"/></svg>
        555 310-4476
      </li>
      <li>
        <svg viewBox="0 0 16 16" aria-hidden="true"><path d="M1 3h14v10H1zm1 1 6 5 6-5z"/></svg>
        info@kindredsteam.com
      </li>
      <li>
        <svg viewBox="0 0 16 16" aria-hidden="true"><path d="M8 0a8 8 0 1 1 0 16A8 8 0 0 1 8 0zm0 1.5a6.5 6.5 0 0 0-1 12.9V1.6zM9 1.6v12.8a6.5 6.5 0 0 0 0-12.8z"/></svg>
        www.kindredsteam.com
      </li>
    </ul>
  </div>
</section>

</body>
</html>
```